Start up Dialysis Clinic needs its first website - Velmira Health

Create a visually appealing and user-friendly website for Velmira Health, a dialysis clinic located in Coral Bay, Lenora Isle. The website should effectively communicate our services to local, regional, and international patients, providing essential information and fostering trust and engagement..
Key Goals:

1. Informative: Provide comprehensive information about our services, facility, and team.
2. User-Friendly: Ensure the website is easy to navigate, with a clear structure and accessible content.
3. Engaging: Create a visually appealing design that reflects the professionalism and care of Velmira Health.
4. Responsive: Ensure the website is fully responsive and performs well on all devices, including desktops, tablets, and smartphones.
5. Trust-Building: Include testimonials, credentials, and patient resources to build trust with potential patients.
Scope of Work:

1. Home Page: An inviting and informative landing page that provides an overview of our clinic, mission, and services. Include a call to action for more information and contact details.
2. About Us: A detailed page about Velmira Health, including our mission, vision, team, and facility tour.
3. Services: A comprehensive page describing the dialysis services we offer, including Hemodialysis, Peritoneal Dialysis, and Home Hemodialysis.
4. Patient Information: A resourceful section with guides for new patients, FAQs, insurance and billing information, and downloadable forms.
5. Resources: Educational content about kidney health, dialysis options, diet and nutrition tips, and support groups.
6. Contact Us: A contact page with our address, phone number, email, office hours, a contact form, and a map.

```html
<!DOCTYPE html>
<html lang="en">
<head>
<meta charset="utf-8">
<title>Velmira Health – Dialysis Clinic in Coral Bay, Lenora Isle</title>
<link rel="stylesheet" href="https://fonts.googleapis.com/css2?family=Ubuntu:wght@500;700&family=Lato:wght@400;700&display=swap">
<style>
:root{
  --blue:#2f7ac0;
  --green:#6aa84f;
  --green-soft:#e6efe0;
  --ink:#222;
  --muted:#666;
  --footer:#10171d;
  --field:#efefef;
}
*{box-sizing:border-box;margin:0;padding:0}
html,body{width:1200px;height:3984px;overflow:hidden}
body{position:relative;font-family:"Lato",sans-serif;color:var(--ink);background:#fff}
.abs{position:absolute}
h1,h2,h3,h4{font-family:"Ubuntu",sans-serif;font-weight:700}
.btn{position:absolute;display:flex;align-items:center;justify-content:center;gap:10px;background:linear-gradient(90deg,var(--blue),var(--green));color:#fff;font-weight:700;font-size:15px;border-radius:2px}
.btn svg{width:12px;height:12px}
.sec-title{position:absolute;left:0;width:1200px;text-align:center;font-size:37px;letter-spacing:1px}
.sec-title .b{color:var(--blue)} .sec-title .g{color:var(--green)}
.divider{position:absolute;left:525px;width:150px;height:1px;background:linear-gradient(90deg,transparent,var(--green),transparent)}
.divider::after{content:"";position:absolute;left:70px;top:-5px;width:10px;height:10px;border-radius:50%;background:var(--green)}
.lead{position:absolute;left:0;width:1200px;text-align:center;font-size:15px;line-height:31px;color:var(--muted)}

.hero{left:0;top:0;width:1200px;height:518px;background:linear-gradient(100deg,#16283a 0%,#2a4a66 45%,#6f8ea6 75%,#41607a 100%);border-top:3px solid var(--green)}
.brand{position:absolute;display:flex;align-items:center;gap:8px;font-family:"Ubuntu",sans-serif;font-weight:700;color:var(--blue)}
.brand i{display:block;background:var(--green)}
.nav{font-size:14px;color:#fff}
.nav a{position:absolute;white-space:nowrap;color:#fff;text-decoration:none}
.hero-sub{left:110px;top:196px;font-size:20px;color:#fff}
.hero-title{left:110px;top:232px;font-size:52px;color:#fff;letter-spacing:1px;font-weight:500}
.hero-text{left:111px;top:296px;width:460px;font-size:15px;line-height:30px;color:#fff}
.scroll-dot{left:578px;top:496px;width:44px;height:44px;border-radius:50%;background:#fff;box-shadow:0 3px 10px rgba(0,0,0,.18)}

.card-img{position:absolute;border-radius:16px}
.card-title{position:absolute;top:1191px;font-family:"Ubuntu",sans-serif;font-weight:700;font-size:20px;letter-spacing:.5px}
.card-arrow{position:absolute;top:1188px;width:36px;height:36px;border-radius:50%;background:var(--green-soft);display:flex;align-items:center;justify-content:center}
.card-arrow svg{width:14px;height:14px}

.about-bg{left:371px;top:1325px;width:829px;height:566px;background:var(--green-soft);border-radius:50px 0 0 50px}
.about-img{left:0;top:1362px;width:589px;height:493px;border-radius:0 14px 14px 0;background:linear-gradient(135deg,#d9dcdc,#9aa1a6 55%,#6c5a48)}
.about-title{left:666px;top:1420px;font-size:37px;color:var(--blue);letter-spacing:1px}
.about-title .g{color:var(--green)}
.about-div{position:absolute;left:666px;top:1487px;width:180px;height:1px;background:linear-gradient(90deg,var(--green),transparent)}
.about-div::after{content:"";position:absolute;left:0;top:-5px;width:10px;height:10px;border-radius:50%;background:var(--green)}
.about-text{position:absolute;left:666px;width:390px;font-size:13px;line-height:27px;color:#555}

.member{position:absolute;top:2121px;width:232px;text-align:center}
.member .photo{height:297px;border-radius:14px}
.member h4{margin-top:26px;font-size:15px;color:var(--ink);font-family:"Lato",sans-serif;font-weight:700}
.member p{margin-top:6px;font-size:13px;color:var(--muted)}
.social-bar{position:absolute;left:27px;bottom:20px;width:178px;height:36px;background:var(--blue);display:flex;align-items:center;justify-content:space-around}
.social-bar span{width:14px;height:14px;border:2px solid #fff;border-radius:3px}

.mission{left:0;top:2586px;width:1200px;height:596px;background:linear-gradient(100deg,#2d4f5c 0%,#6b4a38 35%,#8b9da6 70%,#c9cfd2 100%)}
.mission-card{left:676px;top:2676px;width:451px;height:416px;border-radius:18px;background:linear-gradient(170deg,var(--blue),var(--green));text-align:center;color:#fff}
.mission-card h2{margin-top:42px;font-size:37px;letter-spacing:1px}
.mission-card .wline{margin:16px auto 0;width:200px;height:1px;background:linear-gradient(90deg,transparent,#fff,transparent);position:relative}
.mission-card .wline::after{content:"";position:absolute;left:95px;top:-5px;width:10px;height:10px;border-radius:50%;background:#fff}
.mission-card p{margin:26px auto 0;width:360px;font-size:15px;line-height:31px}
.mission-card p+p{margin-top:30px}
.mission-btn{display:inline-flex;align-items:center;gap:10px;margin-top:24px;padding:0 22px;height:41px;background:#fff;color:var(--blue);font-weight:700;font-size:15px}
.mission-btn svg{width:12px;height:12px}

.field{position:absolute;top:3435px;width:212px;height:54px;background:var(--field);font-size:11px;color:#777;padding:22px 20px}

.footer{left:0;top:3638px;width:1200px;height:346px;background:var(--footer)}
.fcol{position:absolute;top:3716px;color:#fff}
.fcol h4{font-size:19px;letter-spacing:.5px;margin-bottom:14px;font-weight:500}
.fcol li{list-style:none;font-size:13px;line-height:30px}
.copy{left:0;top:3945px;width:1200px;text-align:center;font-size:12px;color:#fff}
</style>
</head>
<body>

<section class="abs hero" role="img" aria-label="Dialysis machine control panel in a clinic"></section>
<div class="brand" style="left:111px;top:52px;font-size:22px"><i style="width:26px;height:26px"></i>Velmira Health</div>
<nav class="abs nav" style="left:0;top:50px;width:1200px">
  <a style="left:363px;color:#6fb0ef">Home</a>
  <a style="left:453px">About Us</a>
  <a style="left:563px">Services</a>
  <a style="left:666px">Patient Information</a>
  <a style="left:846px">Resources</a>
</nav>
<div class="btn" style="left:952px;top:36px;width:135px;height:40px;font-size:14px">Contact Us <svg viewBox="0 0 12 12"><path d="M1 6h9M6 2l4 4-4 4" stroke="#fff" stroke-width="2" fill="none"/></svg></div>
<div class="abs hero-sub">Dialysis clinic in Coral Bay, Lenora Isle</div>
<h1 class="abs hero-title">VELMIRA HEALTH</h1>
<p class="abs hero-text">Sed ut perspiciatis unde omnis iste natus error sit voluptatem accusantium doloremque laudantium, totam rem ape</p>
<div class="btn" style="left:111px;top:371px;width:135px;height:40px">Contact Us <svg viewBox="0 0 12 12"><path d="M1 6h9M6 2l4 4-4 4" stroke="#fff" stroke-width="2" fill="none"/></svg></div>
<div class="abs scroll-dot"></div>

<h2 class="sec-title" style="top:594px"><span class="b">WHAT WE</span> <span class="g">PROVIDE</span></h2>
<div class="divider" style="top:660px"></div>
<p class="lead" style="top:686px">Sed ut perspiciatis unde omnis iste natus error sit voluptatem accusantium doloremque laudantium,<br>totam rem aperiam, eaque ipsa quae ab illo inventore veritatis et quasi architecto bea</p>

<div class="card-img" style="left:97px;top:784px;width:317px;height:376px;background:linear-gradient(160deg,#e9ecee,#b8c4cc 60%,#8a8f94)" role="img" aria-label="Patient receiving hemodialysis with a nurse"></div>
<div class="card-img" style="left:445px;top:784px;width:310px;height:376px;background:#fff;box-shadow:0 6px 20px rgba(0,0,0,.12);padding:6px"><div role="img" aria-label="Dialysis lines connected to a patient's arm" style="width:100%;height:100%;border-radius:12px;background:linear-gradient(150deg,#6f8fb5,#2d4a7a 60%,#1d3560)"></div></div>
<div class="card-img" style="left:785px;top:784px;width:317px;height:376px;background:linear-gradient(160deg,#8a6e52,#c7b9a8 55%,#e8e6e2)" role="img" aria-label="Man resting during home hemodialysis"></div>

<h3 class="card-title" style="left:96px">HEMODIALYSIS</h3>
<div class="card-arrow" style="left:377px"><svg viewBox="0 0 14 14"><path d="M3 11L11 3M5 3h6v6" stroke="var(--green)" stroke-width="1.8" fill="none"/></svg></div>
<h3 class="card-title" style="left:440px;color:var(--blue)">PERITONEAL DIALYSIS</h3>
<div class="card-arrow" style="left:721px;background:linear-gradient(135deg,var(--blue),var(--green))"><svg viewBox="0 0 14 14"><path d="M3 11L11 3M5 3h6v6" stroke="#fff" stroke-width="1.8" fill="none"/></svg></div>
<h3 class="card-title" style="left:784px">HOME HEMODIALYSIS</h3>
<div class="card-arrow" style="left:1066px"><svg viewBox="0 0 14 14"><path d="M3 11L11 3M5 3h6v6" stroke="var(--green)" stroke-width="1.8" fill="none"/></svg></div>

<div class="abs about-bg"></div>
<div class="abs about-img" role="img" aria-label="Clinic treatment room with bed and dialysis machine"></div>
<h2 class="abs about-title">ABOUT <span class="g">OUR</span> CLINIC</h2>
<div class="about-div"></div>
<p class="about-text" style="top:1516px">Sed ut perspiciatis unde omnis iste natus error sit voluptatem accusantium dolo remque laudantium, totam rem aperiam, eaque ipsa quae ab illo inventore verit atis</p>
<p class="about-text" style="top:1611px">Perspiciatis unde omnis iste natus error sit voluptatem accusantium dolo remque laudantium, totam rem aperiam, eaque ipsa quae ab illo inventore verit atis et quasi architecto bea tae vitae dicta sunt explicabo.</p>
<div class="btn" style="left:666px;top:1745px;width:134px;height:41px">Read More <svg viewBox="0 0 12 12"><path d="M1 6h9M6 2l4 4-4 4" stroke="#fff" stroke-width="2" fill="none"/></svg></div>

<h2 class="sec-title" style="top:1972px"><span class="b">OUR TEAM</span> <span class="g">MEMBERS</span></h2>
<div class="divider" style="top:2038px"></div>
<p class="lead" style="top:2061px">Sed ut perspiciatis unde omnis iste natus error sit voluptatem accusantium doloremque laud</p>

<div class="member" style="left:113px"><div class="photo" role="img" aria-label="Portrait of a doctor" style="background:linear-gradient(160deg,#4d7fb0,#e6ecef 60%,#cfd8dc)"></div><h4>Maren Holloway</h4><p>Laborious Physical Exercise</p></div>
<div class="member" style="left:360px"><div class="photo" role="img" aria-label="Portrait of a doctor" style="background:linear-gradient(160deg,#dcdcd6,#f3f3f1 60%,#c9c9c4)"></div><h4>Dorian Vale</h4><p>Laborious Physical Exercise</p></div>
<div class="member" style="left:608px"><div class="photo" role="img" aria-label="Portrait of a nurse" style="position:relative;background:linear-gradient(160deg,#b9c3a8,#a6c2b0 60%,#8fb09a)"><div class="social-bar"><span></span><span></span><span></span></div></div><h4>Lusia Brennt</h4><p>Laborious Physical Exercise</p></div>
<div class="member" style="left:855px"><div class="photo" role="img" aria-label="Portrait of a doctor" style="background:linear-gradient(160deg,#d7d2c6,#efece6 60%,#c4beb2)"></div><h4>Dorian Vale</h4><p>Laborious Physical Exercise</p></div>

<section class="abs mission" role="img" aria-label="Patient resting in a chair during dialysis treatment"></section>
<div class="abs mission-card">
  <h2>OUR MISSION</h2>
  <div class="wline"></div>
  <p>Sed ut perspiciatis unde omnis iste natus error sit voluptatem accusantium doloremque laud antium, totam rem aperiam</p>
  <p>Eaque ipsa quae ab illo inventore veritatis et quasi architecto bea</p>
  <span class="mission-btn">Read More <svg viewBox="0 0 12 12"><path d="M1 6h9M6 2l4 4-4 4" stroke="var(--blue)" stroke-width="2" fill="none"/></svg></span>
</div>

<h2 class="sec-title" style="top:3261px"><span class="b">GET IN TOUCH</span> <span class="g">WITH US</span></h2>
<div class="divider" style="top:3327px"></div>
<p class="lead" style="top:3357px;font-size:13px;line-height:27px">We denounce with righteous indignation and dislike men who are so beguiled and demoralized by the charms of<br>pleasure of the moment</p>
<div class="field" style="left:261px">Full Name</div>
<div class="field" style="left:493px">Email Address</div>
<div class="field" style="left:727px">Contact Number</div>
<div class="btn" style="left:516px;top:3512px;width:167px;height:41px">Send Message <svg viewBox="0 0 12 12"><path d="M1 6h9M6 2l4 4-4 4" stroke="#fff" stroke-width="2" fill="none"/></svg></div>

<footer class="abs footer"></footer>
<div class="brand" style="left:140px;top:3784px;font-size:30px"><i style="width:30px;height:30px"></i>Velmira Health</div>
<div class="fcol" style="left:439px"><h4>QUICK LINKS</h4><ul><li>Home</li><li>About Us</li><li>Our Services</li><li>Patient Information</li><li>Resources</li></ul></div>
<div class="fcol" style="left:671px"><h4>CONTACT US</h4><ul><li>14B, Velmira Health, Coral Bay,</li><li>Lenora Isle</li><li>&nbsp;</li><li>+1 868 555 0142 (Call)</li><li>info@velmirahealth.com (Email)</li></ul></div>
<div class="fcol" style="left:946px"><h4>FOLLOW US</h4><ul><li>Community</li><li>Gallery</li><li>Videos</li><li>Updates</li></ul></div>
<div class="abs copy">(C) Copyright 2024 | All Rights Reserved</div>

</body>
</html>
```